Special Gift Box Design for Torvel Ridge Roasters Vietnam

We need a design for a coffee gift box - the design should reflect the premium quality of our coffee products - it should look elegant, classic, stylish, luxury. We will mostly use the box as a present for our main customers and business partners and sell it in our coffee shops.
The dimensions of the box are 26x10.5x9cm (LxWxH). The Box will contain one bag of coffee (250g) and one Vietnamese coffee filter.
We are a coffee producer in the Central Highlands of Vietnam with a sustainable, fair and inclusive business model. We are producing Arabica coffee from farm to cup. We are sourcing our coffee cherries directly from local farmers which are members of an ethnic minority. Besides Arabica and Specialty Arabicas, we also produce Robusta, blends and herbal coffees with Ginseng and Ganoderma. Our products are sold to 4 and 5-star hotels, in online and retail shops in Vietnam and we will soon start to export our coffee to other countries in Asia and overseas.
We are Greenleaf Accord certified and have received many awards (golden brand of Vietnam, special product from Dalat, typical rural industrial product of Central Vietnam etc.) for our outstanding product quality and our socially responsible business concept. We are a member of the Premium Brew Federation (PBF) and a certified PBF roaster. We are creating stable jobs in a remote and poor area of the Central Highlands.

Have also attached the type of box we will produce with the cover opening on one side

Target Market(s)

For now Vietnam and Thailand, but later also oversea markets, so it should be an international design which can (but no must) have asian/vietnamese elements

Industry/Entity Type

Agriculture, coffee producer

Requirements
Must have
• Our logo must be prominently displayed on the box, otherwise no text or product information will be on the box for now.

```html
<!DOCTYPE html>
<html lang="en">
<head>
<meta charset="utf-8">
<title>Torvel Ridge Roasters – Gift Box</title>
<link href="https://fonts.googleapis.com/css2?family=Teko:wght@600&family=Archivo+Narrow:wght@400&display=swap" rel="stylesheet">
<style>
  :root{
    --bg:#e8e8e8;
    --panel-black:#131211;
    --pattern-dark:#2b2a29;
    --cream:#f2e6bd;
    --gold:#e7c266;
    --coral:#d4545a;
    --red-band:#d6473a;
    --copy-red:#d0412f;
    --kraft:#c9a15c;
    --kraft-ink:#2a1b12;
    --stripe-green:#2f6b35;
  }
  *{margin:0;padding:0;box-sizing:border-box}
  html,body{width:1200px;height:767px;overflow:hidden;background:var(--bg)}
  .canvas{position:relative;width:1200px;height:767px}
  .panel{position:absolute;overflow:hidden}
  .lid-top{left:355px;top:70px;width:780px;height:315px;background:var(--panel-black)}
  .front-face{left:355px;top:385px;width:780px;height:270px;background:var(--panel-black)}
  .end-face{left:40px;top:385px;width:315px;height:270px;background:var(--kraft)}

  .pattern-strip{position:absolute;background:var(--pattern-dark)}
  .lid-top .pattern-strip.left{left:0;top:0;width:26px;height:100%}
  .lid-top .pattern-strip.right{right:0;top:0;width:26px;height:100%}
  .front-face .pattern-strip.right{right:0;top:0;width:22px;height:100%}
  .front-face .pattern-strip.left{left:0;top:0;width:14px;height:100%}
  .end-face .pattern-strip.right{right:0;top:0;width:14px;height:100%}

  .wordmark{position:absolute;display:flex;align-items:center;gap:14px;font-family:"Teko",sans-serif;font-weight:600;line-height:.85;text-transform:uppercase}
  .wordmark .dot{border-radius:50%;flex:none}
  .lid-top .wordmark{left:250px;top:105px;color:var(--cream);font-size:52px}
  .lid-top .wordmark .dot{width:26px;height:26px;background:var(--coral)}
  .front-face .wordmark{left:150px;top:80px;color:var(--gold);font-size:44px}
  .front-face .wordmark .dot{width:22px;height:22px;background:var(--gold)}
  .end-face .wordmark{left:42px;top:120px;color:var(--kraft-ink);font-size:40px}
  .end-face .wordmark .dot{width:20px;height:20px;background:var(--coral)}

  .story-copy{position:absolute;left:545px;top:195px;width:190px;font-family:"Archivo Narrow",sans-serif;font-size:7.5px;line-height:1.45;color:var(--copy-red);text-align:center}
  .story-copy p+p{margin-top:5px}

  .red-band{position:absolute;left:0;bottom:14px;width:100%;height:20px;background:var(--red-band)}
  .front-face .base-line{position:absolute;left:0;bottom:0;width:100%;height:14px;background:var(--panel-black)}

  .end-stripes{position:absolute;left:0;top:14px;width:100%}
  .end-stripes span{display:block;height:5px;margin-bottom:4px}
  .end-stripes .red{background:var(--red-band)}
  .end-stripes .green{background:var(--stripe-green)}
</style>
</head>
<body>
<div class="canvas">

  <section class="panel lid-top" aria-label="Lid top">
    <div class="pattern-strip left" role="img" aria-label="Ethnic textile ornament border"></div>
    <div class="pattern-strip right" role="img" aria-label="Ethnic textile ornament border"></div>
    <div class="wordmark"><span class="dot"></span><span>Torvel Ridge<br>Roasters</span></div>
    <div class="story-copy">
      <p>Grown slowly on high ridges and picked by hand at full ripeness, every bean is washed, dried and roasted in small batches for a clean, sweet cup.</p>
      <p>Brew it the traditional way with the filter inside this box and share it with the people you value most.</p>
    </div>
  </section>

  <section class="panel front-face" aria-label="Front side">
    <div class="pattern-strip left" role="img" aria-label="Ethnic textile ornament border"></div>
    <div class="pattern-strip right" role="img" aria-label="Ethnic textile ornament border"></div>
    <div class="wordmark"><span class="dot"></span><span>Torvel Ridge<br>Roasters</span></div>
    <div class="red-band"></div>
    <div class="base-line"></div>
  </section>

  <section class="panel end-face" aria-label="End side">
    <div class="end-stripes">
      <span class="red"></span><span class="green"></span><span class="red"></span><span class="red"></span>
    </div>
    <div class="pattern-strip right" role="img" aria-label="Ethnic textile ornament border"></div>
    <div class="wordmark"><span class="dot"></span><span>Torvel Ridge<br>Roasters</span></div>
  </section>

</div>
</body>
</html>
```